Calvanto Group Real Estate Company business cards

New business card design, we are generally happy with the basic layout of the existing front of business card, (feel free to change) but require a head shot photo on the back side.

http://www.calvanto.com.au/

Attached logos, and existing business card

------------------------------

Target Market(s)

Real estate

Industry/Entity Type

Real Estate

Contact Information for Business Card

Standard size double sided

Font styles to use
Other font styles liked:
• Futura

Requirements
Must have
• Photo head shot on the back side
Nice to have
• yes
Should not have
• No

```html
<!DOCTYPE html>
<html lang="en">
<head>
<meta charset="utf-8">
<title>Calvanto Group – Business Cards</title>
<link href="https://fonts.googleapis.com/css2?family=Jost:wght@400;500;600&family=Roboto:wght@400;700&display=swap" rel="stylesheet">
<style>
  :root {
    --bg: #e4e4e6;
    --card: #f7f7f8;
    --purple: #2a1a4e;
    --orange: #ee7d1a;
    --rule: #9a9aa0;
    --text: #2a2340;
  }
  * { box-sizing: border-box; margin: 0; padding: 0; }
  html, body { width: 1200px; height: 1200px; overflow: hidden; }
  body {
    background: var(--bg);
    font-family: "Jost", "Futura", sans-serif;
    color: var(--text);
    position: relative;
  }
  .card {
    position: absolute;
    left: 180px;
    width: 840px;
    height: 480px;
    background: var(--card);
    border-radius: 28px;
    overflow: hidden;
    box-shadow: 0 6px 18px rgba(0,0,0,0.18);
  }
  .card--front { top: 90px; }
  .card--back { top: 630px; }
  .card svg.bands { position: absolute; inset: 0; }

  /* Front */
  .headshot {
    position: absolute;
    left: 0; bottom: 0;
    width: 360px; height: 350px;
    background: linear-gradient(180deg, #d9d3cf 0%, #c9b3a3 45%, #2b3550 75%, #222b45 100%);
  }
  .tagline {
    position: absolute;
    right: 60px; top: 100px;
    text-align: right;
    font-size: 32px;
    line-height: 1.1;
    font-weight: 400;
    letter-spacing: 0.5px;
  }
  .tagline-line { color: var(--purple); display: block; }
  .tagline-accent { color: var(--orange); display: block; }
  .brand-name {
    font-family: "Jost", "Futura", sans-serif;
    font-weight: 500;
    color: var(--purple);
    white-space: nowrap;
  }
  .card--front .brand-name {
    position: absolute;
    right: 60px; top: 200px;
    font-size: 54px;
    letter-spacing: 0.5px;
  }

  /* Back */
  .card--back .brand-name {
    position: absolute;
    left: 60px; top: 150px;
    font-size: 64px;
    letter-spacing: 0.5px;
  }
  .person {
    position: absolute;
    right: 60px; top: 72px;
    text-align: right;
  }
  .person-name {
    font-family: "Roboto", sans-serif;
    font-weight: 700;
    font-size: 28px;
    color: var(--purple);
  }
  .person-role {
    font-family: "Roboto", sans-serif;
    font-size: 16px;
    color: var(--text);
    margin-top: 2px;
  }
  .divider {
    position: absolute;
    left: 100px; right: 50px; top: 262px;
    height: 1px;
    background: var(--rule);
  }
  .social {
    position: absolute;
    right: 60px; top: 150px;
    display: flex; align-items: center; gap: 7px;
    font-family: "Roboto", sans-serif;
    font-size: 18px;
  }
  .social-label { margin-right: 8px; }
  .social-dot {
    width: 22px; height: 22px;
    border-radius: 5px;
    background: var(--orange);
  }
  .abn {
    position: absolute;
    right: 60px; top: 192px;
    font-family: "Roboto", sans-serif;
    font-size: 18px;
    letter-spacing: 0.5px;
  }
  .contacts {
    position: absolute;
    left: 100px; top: 282px;
    list-style: none;
    font-family: "Roboto", sans-serif;
    font-size: 21px;
    letter-spacing: 0.3px;
  }
  .contact-item {
    display: flex; align-items: center; gap: 14px;
    height: 34px;
  }
  .contact-icon { width: 20px; height: 20px; flex: none; }
</style>
</head>
<body>

<section class="card card--front" aria-label="Business card front">
  <svg class="bands" width="840" height="480" viewBox="0 0 840 480" aria-hidden="true">
    <polygon points="360,440 800,440 840,420 840,480 360,480" fill="#2a1a4e"/>
  </svg>
  <div class="headshot" role="img" aria-label="Head shot photo of the director in a dark suit and blue tie"></div>
  <p class="tagline">
    <span class="tagline-line">Let us show you</span>
    <span class="tagline-accent">property</span>
  </p>
  <div class="brand-name">calvanto group</div>
</section>

<section class="card card--back" aria-label="Business card back">
  <svg class="bands" width="840" height="480" viewBox="0 0 840 480" aria-hidden="true">
    <polygon points="644,380 840,380 840,420 610,420" fill="#2a1a4e"/>
    <polygon points="0,455 580,455 610,420 840,420 840,480 0,480" fill="#ee7d1a"/>
  </svg>

  <div class="brand-name">calvanto group</div>

  <div class="person">
    <div class="person-name">Daniel Tran</div>
    <div class="person-role">Director</div>
  </div>

  <div class="social">
    <span class="social-label">Find us:</span>
    <span class="social-dot"></span>
    <span class="social-dot"></span>
    <span class="social-dot"></span>
  </div>
  <div class="abn">ABN: 12 345 678 901</div>

  <div class="divider"></div>

  <ul class="contacts">
    <li class="contact-item">
      <svg class="contact-icon" viewBox="0 0 20 20" aria-hidden="true">
        <rect x="4" y="1" width="12" height="18" rx="2" fill="#ee7d1a"/>
        <rect x="6" y="4" width="8" height="10" fill="#fff"/>
        <circle cx="10" cy="16.5" r="1" fill="#fff"/>
      </svg>
      <span>0400 555 218</span>
    </li>
    <li class="contact-item">
      <svg class="contact-icon" viewBox="0 0 20 20" aria-hidden="true">
        <circle cx="10" cy="10" r="8.5" fill="#ee7d1a"/>
        <ellipse cx="10" cy="10" rx="3.5" ry="8.5" fill="none" stroke="#fff" stroke-width="1.2"/>
        <line x1="1.5" y1="10" x2="18.5" y2="10" stroke="#fff" stroke-width="1.2"/>
        <line x1="3" y1="6" x2="17" y2="6" stroke="#fff" stroke-width="1"/>
        <line x1="3" y1="14" x2="17" y2="14" stroke="#fff" stroke-width="1"/>
      </svg>
      <span>www.calvanto.com.au</span>
    </li>
    <li class="contact-item">
      <svg class="contact-icon" viewBox="0 0 20 20" aria-hidden="true">
        <rect x="1" y="4" width="18" height="12" rx="1.5" fill="#ee7d1a"/>
        <polyline points="1.5,5 10,11 18.5,5" fill="none" stroke="#fff" stroke-width="1.4"/>
      </svg>
      <span>daniel.tran@calvanto.com.au</span>
    </li>
  </ul>
</section>

</body>
</html>
```